OBK Farcoast Logistics Limited

We need the buissnes card to be very exclusive. As we are all young in our company. We need this to be the gate to make our clients feel deep interest for us.

We are focused in as International Trade advisors, and our products go from Oil Tanker Ships to Rubber balls for dogs.

Our Slogan is Bringing Far Shores Near.
And our main marketing will be through Internet.

We were stablished in 2009 In Mexico and we also have offices in Hong Kong.
We have representatives in China and Europe.

Target Market(s)

Is every company or Individual that wants to develop an International Project or product development or Logistic service of Goods and people.
Some of our current projects are Ship Brokerage, Mine Brokerage, Real State and Product Pormotional development.

Industry/Entity Type

It Company

Requirements
Must have
• Our Logo and slogan, and make the card accoriding to the logo.
Nice to have
• Our Colors

```html
<!DOCTYPE html>
<html lang="en">
<head>
<meta charset="utf-8">
<title>OBK Farcoast Logistics Limited – Business Card</title>
<link rel="stylesheet" href="https://fonts.googleapis.com/css2?family=Open+Sans:wght@400;600;700&display=swap">
<style>
  :root {
    --page-bg: #e9e7e3;
    --silver-light: #f4f4f4;
    --silver-mid: #dcdcdc;
    --silver-dark: #c4c4c4;
    --panel: rgba(255, 255, 255, 0.55);
    --brand-green: #8cc63f;
    --brand-blue: #1e9ad6;
    --brand-navy: #2b3990;
    --ink: #3a3a3a;
    --ink-soft: #5a5a5a;
  }
  * { box-sizing: border-box; margin: 0; padding: 0; }
  html, body {
    width: 1200px;
    height: 720px;
    overflow: hidden;
  }
  body {
    background: var(--page-bg);
    font-family: "Open Sans", Arial, sans-serif;
    position: relative;
  }
  .card {
    position: absolute;
    top: 200px;
    width: 560px;
    height: 320px;
    border-radius: 4px;
    overflow: hidden;
    background:
      repeating-linear-gradient(0deg, rgba(255,255,255,0.12) 0 1px, rgba(0,0,0,0.025) 1px 2px),
      linear-gradient(135deg, var(--silver-light) 0%, var(--silver-mid) 45%, var(--silver-light) 70%, var(--silver-dark) 100%);
    box-shadow: 0 6px 18px rgba(0,0,0,0.18);
  }
  .card--front { left: 25px; }
  .card--back { left: 615px; }

  /* front */
  .card__bands { position: absolute; inset: 0; width: 100%; height: 100%; }
  .brand-block {
    position: absolute;
    left: 40px;
    top: 70px;
    width: 210px;
    text-align: center;
  }
  .brand-block__mark {
    display: block;
    margin: 0 auto 10px;
    width: 70px;
    height: 70px;
    border-radius: 50%;
    background: var(--brand-blue);
  }
  .brand-block__name {
    font-weight: 700;
    font-size: 44px;
    letter-spacing: 4px;
    color: var(--brand-green);
    line-height: 1;
  }
  .brand-block__slogan {
    margin-top: 4px;
    font-size: 11px;
    color: var(--brand-blue);
    white-space: nowrap;
  }
  .contact {
    position: absolute;
    left: 290px;
    top: 34px;
    width: 250px;
  }
  .contact__name {
    font-size: 18px;
    font-weight: 700;
    color: var(--brand-green);
    line-height: 1.1;
  }
  .contact__position {
    font-size: 12px;
    font-weight: 600;
    color: var(--brand-blue);
    margin-bottom: 16px;
  }
  .contact__list { list-style: none; }
  .contact__item {
    display: flex;
    align-items: flex-start;
    gap: 9px;
    font-size: 13px;
    color: var(--ink);
    line-height: 1.3;
    margin-bottom: 9px;
  }
  .contact__icon { width: 13px; height: 13px; flex: none; margin-top: 2px; fill: var(--ink); }
  .contact__web {
    position: absolute;
    right: 22px;
    top: 258px;
    font-size: 13px;
    font-weight: 700;
    letter-spacing: 1.2px;
    color: var(--ink);
    line-height: 22px;
  }

  /* back */
  .back-mark {
    position: absolute;
    left: 0;
    right: 0;
    top: 78px;
    display: flex;
    align-items: center;
    justify-content: center;
    gap: 16px;
  }
  .back-mark__dot {
    width: 64px;
    height: 64px;
    border-radius: 50%;
    background: var(--brand-blue);
  }
  .back-mark__name {
    font-size: 72px;
    font-weight: 700;
    letter-spacing: 6px;
    color: var(--brand-navy);
    line-height: 1;
  }
  .back-web {
    position: absolute;
    left: 0;
    right: 0;
    top: 250px;
    text-align: center;
    font-size: 19px;
    letter-spacing: 3px;
    color: var(--ink-soft);
  }
  .back-web__domain { color: var(--brand-blue); }
</style>
</head>
<body>

<section class="card card--front" aria-label="Business card front">
  <svg class="card__bands" viewBox="0 0 560 320" preserveAspectRatio="none" aria-hidden="true">
    <rect class="panel" x="262" y="0" width="298" height="256" fill="var(--panel)"/>
    <polygon points="322,256 560,256 560,280 308,280" fill="var(--brand-green)"/>
    <polygon points="0,280 308,280 292,302 0,302" fill="var(--brand-blue)"/>
  </svg>

  <div class="brand-block">
    <span class="brand-block__mark"></span>
    <div class="brand-block__name">OBK</div>
    <div class="brand-block__slogan">Bringing Far Shores Near</div>
  </div>

  <div class="contact">
    <div class="contact__name">Your Name</div>
    <div class="contact__position">Position</div>
    <ul class="contact__list">
      <li class="contact__item">
        <svg class="contact__icon" viewBox="0 0 16 16" aria-hidden="true"><path d="M3.5 1l2.6 3-1.4 1.8c.9 1.9 2.3 3.3 4.2 4.2l1.8-1.4 3 2.6-1.5 2.6C6.6 13.5 2.5 9.4 1 3.4z"/></svg>
        <span>123-456-7890</span>
      </li>
      <li class="contact__item">
        <svg class="contact__icon" viewBox="0 0 16 16" aria-hidden="true"><path d="M5 0h6a1 1 0 0 1 1 1v14a1 1 0 0 1-1 1H5a1 1 0 0 1-1-1V1a1 1 0 0 1 1-1zm0 2v10h6V2zm3 11a1 1 0 1 0 0 2 1 1 0 0 0 0-2z"/></svg>
        <span>123-456-7890</span>
      </li>
      <li class="contact__item">
        <svg class="contact__icon" viewBox="0 0 16 16" aria-hidden="true"><path d="M1 3h14v10H1zm1.5 1.2v.4L8 8.6l5.5-4v-.4zm0 2.2v5.4h11V6.4L8 10.3z"/></svg>
        <span>info@farcoast.com</span>
      </li>
      <li class="contact__item">
        <svg class="contact__icon" viewBox="0 0 16 16" aria-hidden="true"><path d="M8 0a5.5 5.5 0 0 1 5.5 5.5C13.5 10 8 16 8 16S2.5 10 2.5 5.5A5.5 5.5 0 0 1 8 0zm0 3.3a2.2 2.2 0 1 0 0 4.4 2.2 2.2 0 0 0 0-4.4z"/></svg>
        <span>00, Complex Name<br>City, State, 00045</span>
      </li>
    </ul>
  </div>

  <div class="contact__web">www.farcoast.com</div>
</section>

<section class="card card--back" aria-label="Business card back">
  <div class="back-mark">
    <span class="back-mark__dot"></span>
    <span class="back-mark__name">OBK</span>
  </div>
  <div class="back-web">www.<span class="back-web__domain">farcoast</span>.com</div>
</section>

</body>
</html>
```